Lotstallmart.com Webpage Design

Design Brief for lotstallmart.com (Copy of Brief also in attached Word file)

Name of Website- lotstallmart.com (existing logo and look & feel of website to be changed)

Logo - Finalised. The logo files are attached with the brief as “logo.jpeg”. The “Blue- Grey” version of the logo is for use on lighter backgrounds and the “Orange-White” version of the logo is for use on darker backgrounds. (A full Black version of the logo is also attached). Both versions may be used in different parts of the website. All attached files are in .png format.
Status - The website in functional and is undergoing user trials. However, we want to improve the look & feel of the website so at it seems
a. cotemporary,
b. Easy to Navigate
c. professional and
d. Vibrant.

Please visit ‘lotstallmart.com’ to check out the website and its functionalities – please use it only as a reference for the features & functions to be provided, however the designer should use a ‘Free Hand’ in designing the composition of various parts of the webpage without getting too influenced by the existing design

Objective of the Website ‘lotstallmart.com –
a. It is a portal focussed on listing of ‘Retail’ specific real-estate properties by developers, owners and realty brokers. The properties shall listed under the following four categories-
i. Retail Malls
ii. Shopping Complexes
iii. High-street shops
iv. Retail Warehouses
*refer lotstallmart.com for better clarity

b. The abovementioned properties shall be listed either for ‘Sale’ or ‘rent\lease’ or both

c. Users shall visit the site in case they wish to acquire a retail \ shop space either on ‘sale’ or ‘rent’. These Users would be able to specify the ‘Search Criteria’ through the tool-bars provided on the website – the ‘Search Criteria’ shall comprise of ‘Type of space category’, ‘City’, ‘Locality’, transaction type ie ‘Rent \ Sale’ and ‘Area Range’

d. The main revenue model for the website shall be listing fee ( or advertising charges ) payable by those listing their properties on the website.

Three Main Pages of Website (lotstallmart.com) that need to be designed -
a. Main Home Page (visit the web link - http://lotstallmart.com/ ) - The main home page has the “Search Toolbar” for specifying of Search Criteria by the User. It shall also have the following features & functions-
i. Main Advertising Banner
ii. Featured Projects
iii. New Launches
iv. Toolbar with buttons – ‘Advertise with Us’, ‘Listings Alert’, ‘Mart Wizards’, ‘Advertiser Login’

b. Property Listings Page (visit the web link - http://lotstallmart.com/gurgaon-in-india ) - The List of property options that match the Criteria specified by the ‘User’ get displayed on this page.

c. Property Detail Page - When the ‘User’ clicks on the “More….” Button on the ‘Property Listings Page’ (given in point b. above) the web page with the details of the property opens. (For Example – visit the web link - http://lotstallmart.com/vorne-Shopping-Complex-vorne-quadrion-gurgaon-636 )

Note:- Please refer to attached ‘Shopping’ related images the designer may use them on the website to provide a look & feel of retail if required – either separately or rotate in a single window

Target Market(s)

Retailers & Investors looking for retail space, Real Estate Brokers, Developers

Industry/Entity Type

Advertising

Number of Pages Required

3 page

Requirements
Must have
• Refer to existing site lotstallmart.com -- all the existing functionalities are a must have.
Nice to have
• The Designer may use the retail related images on the website if required for making it more vibrant. Refer attached images Shopping(1-6).jpg

```html
<!DOCTYPE html>
<html lang="en">
<head>
<meta charset="utf-8">
<title>Lotstallmart.com – Retail Space Portal</title>
<link rel="stylesheet" href="https://fonts.googleapis.com/css2?family=Open+Sans:wght@400;600;700&display=swap">
<style>
:root{
  --navy:#0b3a68;
  --navy-deep:#08305a;
  --blue:#1596f2;
  --blue-title:#1a8ae0;
  --orange:#f26522;
  --green:#8dc63f;
  --ink:#333;
  --muted:#777;
  --light:#eeeeee;
  --line:#d6d6d6;
}
*{box-sizing:border-box;margin:0;padding:0}
html,body{width:1200px;height:4337px;overflow:hidden}
body{font-family:"Open Sans",Arial,sans-serif;color:var(--ink);background:var(--light);position:relative}
.abs{position:absolute}

/* top bar */
.topbar{left:0;top:0;width:1200px;height:23px;background:var(--navy);color:#fff;font-size:11px}
.topbar .cities{position:absolute;left:88px;top:4px}
.topbar .list{position:absolute;right:80px;top:4px}

/* header */
.header{left:0;top:23px;width:1200px;height:87px;background:#fff}
.brand{position:absolute;left:88px;top:12px;display:flex;align-items:center;gap:10px}
.brand-dot{width:44px;height:44px;border-radius:50%;background:var(--blue)}
.brand-name{font-size:38px;font-weight:700;color:var(--blue);line-height:1}
.brand-tag{position:absolute;left:142px;top:58px;font-size:8px;color:var(--muted);letter-spacing:.5px}
.nav{position:absolute;top:26px;left:549px;display:flex;gap:14px}
.nav a{display:block;height:32px;line-height:30px;padding:0 16px;font-size:12px;color:var(--ink);text-decoration:none;border:1px solid var(--line);background:#fff}
.nav a.home{background:var(--navy);color:#fff;border-color:var(--navy)}
.nav a.login{background:var(--green);color:#fff;border-color:var(--green)}
.nav-sub{position:absolute;left:997px;top:62px;font-size:9px;color:var(--muted)}

/* hero */
.hero{left:0;top:110px;width:1200px;height:520px;background:linear-gradient(180deg,#3a2b22 0%,#5a4536 40%,#2b211b 100%)}
.search-panel{left:237px;top:202px;width:723px;height:361px;background:#fff;box-shadow:0 2px 8px rgba(0,0,0,.3)}
.format{position:absolute;left:0;top:0;width:410px;height:361px;text-align:center}
.format svg{position:absolute;left:183px;top:60px}
.format h2{position:absolute;left:0;width:100%;top:100px;font-size:33px;font-weight:400;color:var(--blue-title)}
.format .meaning{position:absolute;width:100%;top:150px;font-size:12px;color:var(--orange)}
.format .rule{position:absolute;left:175px;top:187px;width:60px;border-top:1px solid var(--line)}
.checks{position:absolute;left:55px;top:220px;width:330px;display:grid;grid-template-columns:170px 160px;row-gap:14px;text-align:left;font-size:12px;color:var(--muted)}
.checks label{display:flex;align-items:center;gap:8px}
.checks .box{width:15px;height:15px;border:1px solid #bbb;display:inline-block;position:relative}
.checks .box.on::after{content:"";position:absolute;left:4px;top:0;width:5px;height:10px;border:solid var(--blue);border-width:0 2px 2px 0;transform:rotate(45deg)}
.fields{position:absolute;left:425px;top:55px;width:257px}
.field{height:35px;border:1px solid #bdd3e6;margin-bottom:6px;font-size:12px;color:#555;line-height:33px;padding-left:10px;position:relative;background:#fff}
.field.first{border-color:var(--blue);margin-bottom:17px}
.field.sel::after{content:"";position:absolute;right:0;top:0;width:24px;height:33px;background:#f3f3f3;border-left:1px solid #ddd}
.field.sel::before{content:"";position:absolute;right:8px;top:14px;border:4px solid transparent;border-top-color:#666;z-index:1}
.search-btn{height:36px;background:var(--navy);color:#fff;text-align:center;line-height:36px;font-size:15px;margin-top:4px}

/* categories */
.categories{left:0;top:630px;width:1200px;height:405px;background:var(--blue)}
.cat-tab{position:absolute;right:88px;top:6px;width:116px;height:28px;background:#0f80d6;color:#fff;font-size:12px;line-height:28px;padding-left:14px}
.cat-tab::after{content:"";position:absolute;right:10px;top:6px;width:16px;height:16px;border-radius:50%;background:#fff}
.cat-tab::before{content:"";position:absolute;right:14px;top:13px;width:6px;height:6px;border-left:2px solid #0f80d6;border-top:2px solid #0f80d6;transform:rotate(45deg);z-index:1}
.cat{position:absolute;top:65px;width:220px;text-align:center;color:#fff;font-size:17px;font-weight:600;line-height:1.3}
.cat .disc{width:208px;height:208px;margin:0 auto 22px;border-radius:50%;border:6px solid #fff;box-shadow:0 2px 6px rgba(0,0,0,.25)}

/* listing sections */
.section-title{position:absolute;left:0;width:1200px;text-align:center;font-size:34px;font-weight:400;color:#222}
.across{position:absolute;left:0;width:1200px;text-align:center;font-size:10px;color:var(--muted)}
.across span{display:inline-block;padding:0 10px;position:relative}
.across span::before,.across span::after{content:"";position:absolute;top:7px;width:50px;border-top:1px solid #888}
.across span::before{right:100%}
.across span::after{left:100%}
.grid{position:absolute;left:0;width:1200px;display:grid;grid-template-columns:repeat(4,292px);column-gap:10.6px;row-gap:20px}
.card{height:405px;background:#fff;position:relative;text-align:center}
.card .photo{height:222px}
.card h3{position:absolute;top:254px;width:100%;font-size:18px;font-weight:600;color:var(--blue-title);white-space:nowrap}
.card .kind{position:absolute;top:282px;width:100%;font-size:15px;color:#444}
.card svg{position:absolute;left:139px;top:318px}
.card .loc{position:absolute;top:350px;width:100%;font-size:11px;color:#555}
.view{position:absolute;left:87px;top:98px;width:118px;height:34px;background:var(--orange);color:#fff;font-size:12px;line-height:34px}

/* dark band */
.extras{left:0;top:3251px;width:1200px;height:607px;background:var(--navy)}
.col{position:absolute;top:0;color:#fff}
.col h4{position:absolute;top:100px;width:100%;text-align:center;font-size:24px;font-weight:600}
.col p{position:absolute;top:145px;width:100%;text-align:center;font-size:11px;line-height:1.4}
.input{position:absolute;height:36px;border:1px solid #4f7aa3;font-size:11px;color:#b8cde0;line-height:34px;padding-left:12px}
.input.sel::after{content:"";position:absolute;right:-1px;top:-1px;width:22px;height:36px;border:1px solid #4f7aa3}
.hint{position:absolute;font-size:9px;color:#b8cde0}
.btn{position:absolute;height:36px;background:var(--blue);color:#fff;text-align:center;line-height:36px;font-size:13px}
.editor-img{position:absolute;left:462px;top:159px;width:246px;height:160px;background:linear-gradient(180deg,#cfe3f5 0%,#8fb3d6 60%,#4a6a8c 100%)}

/* footer */
.footer{left:0;top:3858px;width:1200px;height:479px;background:var(--blue);color:#fff}
.footer .brand{left:92px;top:67px}
.footer .brand-dot{background:#fff}
.footer .brand-name{color:#fff;font-size:40px}
.footer h5{position:absolute;top:84px;font-size:14px;font-weight:600}
.links{position:absolute;top:116px;font-size:11px;line-height:19px;list-style:none}
.about{position:absolute;left:775px;top:116px;width:340px;font-size:11px;line-height:15px}
.rule-w{position:absolute;top:252px;left:462px;width:650px;border-top:1px solid rgba(255,255,255,.5)}
.social{position:absolute;left:530px;top:268px;display:flex;gap:16px}
.social span{width:22px;height:22px;border-radius:50%;background:#fff;opacity:.9}
.rule-c{position:absolute;top:304px;left:380px;width:440px;border-top:1px solid rgba(255,255,255,.5)}
.addr{position:absolute;left:0;width:1200px;text-align:center;font-size:11px;line-height:22px}
</style>
</head>
<body>

<div class="abs topbar"><span class="cities">Cities</span><span class="list">List Your Property Here</span></div>

<header class="abs header">
  <div class="brand"><span class="brand-dot"></span><span class="brand-name">lotstallmart</span></div>
  <div class="brand-tag">INDIA'S LEADING PORTAL FOR RETAIL SPACE</div>
  <nav class="nav">
    <a class="home">Home</a><a>Advertise with Us</a><a>Mart Wizards</a><a>Listing Alert</a><a class="login">Advertiser Login</a>
  </nav>
  <div class="nav-sub">New Advertiser · Register</div>
</header>

<div class="abs hero" role="img" aria-label="Photo of a busy shopping mall interior with shoppers"></div>

<div class="abs search-panel">
  <div class="format">
    <svg width="40" height="40" viewBox="0 0 40 40"><circle cx="17" cy="15" r="11" fill="none" stroke="#1a8ae0" stroke-width="3.5"/><line x1="10" y1="23" x2="3" y2="36" stroke="#1a8ae0" stroke-width="4" stroke-linecap="round"/></svg>
    <h2>Select Retail Format</h2>
    <div class="meaning">B-Meaning of Retail Format</div>
    <div class="rule"></div>
    <div class="checks">
      <label><span class="box on"></span>Retail Malls</label>
      <label><span class="box"></span>High Street Shops</label>
      <label><span class="box"></span>Shopping Complex</label>
      <label><span class="box"></span>Retail Warehouses</label>
    </div>
  </div>
  <div class="fields">
    <div class="field first">Enter Keywords</div>
    <div class="field sel">Sale Or Rent Or Both</div>
    <div class="field sel">Select City</div>
    <div class="field sel">Select Locality/Micro-Market</div>
    <div class="field sel">Select Locality/Micro-Market</div>
    <div class="search-btn">SEARCH NOW</div>
  </div>
</div>

<section class="abs categories">
  <div class="cat-tab">Categories</div>
  <div class="cat" style="left:156px"><div class="disc" role="img" aria-label="Woman carrying shopping bags" style="background:linear-gradient(160deg,#f0a24a,#c9622a)"></div>Retail Malls</div>
  <div class="cat" style="left:381px"><div class="disc" role="img" aria-label="Group of shoppers with bags" style="background:linear-gradient(160deg,#b9c27a,#7a6a4a)"></div>Shopping<br>Complexes</div>
  <div class="cat" style="left:607px"><div class="disc" role="img" aria-label="Shopper on a high street" style="background:linear-gradient(160deg,#d8d0c8,#6b5a50)"></div>High-Street<br>Shops</div>
  <div class="cat" style="left:832px"><div class="disc" role="img" aria-label="Shoppers in a retail warehouse" style="background:linear-gradient(160deg,#d2c4b0,#8a7560)"></div>Retail<br>Warehouses</div>
</section>

<h2 class="section-title" style="top:1150px">Featured Retail Projects</h2>
<div class="across" style="top:1208px"><span>Across India</span></div>
<div class="grid" style="top:1272px">
  <div class="card"><div class="photo" role="img" aria-label="Shopping complex exterior" style="background:linear-gradient(180deg,#6b7a86,#3f4a52)"></div><div class="view">View the listing</div><h3>Meridian Arcade</h3><div class="kind">Shopping Complex</div><svg width="14" height="18" viewBox="0 0 14 18"><path d="M7 17C7 17 1 10 1 6.5A6 6 0 0 1 13 6.5C13 10 7 17 7 17Z" fill="none" stroke="#999"/><circle cx="7" cy="6.5" r="2" fill="#999"/></svg><div class="loc">Surat - Althan</div></div>
  <div class="card"><div class="photo" role="img" aria-label="Lit shopping complex at dusk" style="background:linear-gradient(180deg,#3b5a8a,#8a7a60)"></div><h3>Sector Row 81</h3><div class="kind">Shopping Complex</div><svg width="14" height="18" viewBox="0 0 14 18"><path d="M7 17C7 17 1 10 1 6.5A6 6 0 0 1 13 6.5C13 10 7 17 7 17Z" fill="none" stroke="#999"/><circle cx="7" cy="6.5" r="2" fill="#999"/></svg><div class="loc">Faridabad - Sector 81</div></div>
  <div class="card"><div class="photo" role="img" aria-label="Tall tower at night" style="background:linear-gradient(180deg,#1d3d70,#b0843a)"></div><h3>Aurum 24</h3><div class="kind">Retail Malls</div><svg width="14" height="18" viewBox="0 0 14 18"><path d="M7 17C7 17 1 10 1 6.5A6 6 0 0 1 13 6.5C13 10 7 17 7 17Z" fill="none" stroke="#999"/><circle cx="7" cy="6.5" r="2" fill="#999"/></svg><div class="loc">Sohna Road - Gurgaon</div></div>
  <div class="card"><div class="photo" role="img" aria-label="Glass fronted mall" style="background:linear-gradient(180deg,#8fb8dd,#c8d6e0)"></div><h3>Harbor Mall</h3><div class="kind">Retail Malls</div><svg width="14" height="18" viewBox="0 0 14 18"><path d="M7 17C7 17 1 10 1 6.5A6 6 0 0 1 13 6.5C13 10 7 17 7 17Z" fill="none" stroke="#999"/><circle cx="7" cy="6.5" r="2" fill="#999"/></svg><div class="loc">New Delhi - Tagore Garden</div></div>
  <div class="card"><div class="photo" role="img" aria-label="Mall entrance facade" style="background:linear-gradient(180deg,#7fa6c8,#8a7058)"></div><h3>Skyline Walk Mall</h3><div class="kind">Shopping Complex</div><svg width="14" height="18" viewBox="0 0 14 18"><path d="M7 17C7 17 1 10 1 6.5A6 6 0 0 1 13 6.5C13 10 7 17 7 17Z" fill="none" stroke="#999"/><circle cx="7" cy="6.5" r="2" fill="#999"/></svg><div class="loc">Chennai - Aminjikarai</div></div>
  <div class="card"><div class="photo" role="img" aria-label="Red and white mall building" style="background:linear-gradient(180deg,#9ab8d6,#a8524a)"></div><h3>The Regal Mall</h3><div class="kind">Shopping Complex</div><svg width="14" height="18" viewBox="0 0 14 18"><path d="M7 17C7 17 1 10 1 6.5A6 6 0 0 1 13 6.5C13 10 7 17 7 17Z" fill="none" stroke="#999"/><circle cx="7" cy="6.5" r="2" fill="#999"/></svg><div class="loc">Chennai - Velacheri</div></div>
  <div class="card"><div class="photo" role="img" aria-label="Office and retail tower render" style="background:linear-gradient(90deg,#7a8c9a,#c9b14a)"></div><h3>Zenith One Centre</h3><div class="kind">Retail Malls</div><svg width="14" height="18" viewBox="0 0 14 18"><path d="M7 17C7 17 1 10 1 6.5A6 6 0 0 1 13 6.5C13 10 7 17 7 17Z" fill="none" stroke="#999"/><circle cx="7" cy="6.5" r="2" fill="#999"/></svg><div class="loc">Gurgaon - Golf Course Road</div></div>
  <div class="card"><div class="photo" role="img" aria-label="Modern glass towers" style="background:linear-gradient(180deg,#a9c4dc,#6f8599)"></div><h3>Harbor Mall</h3><div class="kind">Retail Malls</div><svg width="14" height="18" viewBox="0 0 14 18"><path d="M7 17C7 17 1 10 1 6.5A6 6 0 0 1 13 6.5C13 10 7 17 7 17Z" fill="none" stroke="#999"/><circle cx="7" cy="6.5" r="2" fill="#999"/></svg><div class="loc">Gurgaon - Sohna Road</div></div>
</div>

<h2 class="section-title" style="top:2214px">Featured New Launches</h2>
<div class="across" style="top:2272px"><span>Across India</span></div>
<div class="grid" style="top:2335px">
  <div class="card"><div class="photo" role="img" aria-label="Mall atrium interior" style="background:linear-gradient(180deg,#7b8f99,#4d5a5e)"></div><h3>The Grand Bazaar Place</h3><div class="kind">Retail Malls</div><svg width="14" height="18" viewBox="0 0 14 18"><path d="M7 17C7 17 1 10 1 6.5A6 6 0 0 1 13 6.5C13 10 7 17 7 17Z" fill="none" stroke="#999"/><circle cx="7" cy="6.5" r="2" fill="#999"/></svg><div class="loc">Bhopal - Kolar Road</div></div>
  <div class="card"><div class="photo" role="img" aria-label="Mall corridor with shops" style="background:linear-gradient(180deg,#5a4a3c,#a88a62)"></div><h3>Tide One</h3><div class="kind">Shopping Complex</div><svg width="14" height="18" viewBox="0 0 14 18"><path d="M7 17C7 17 1 10 1 6.5A6 6 0 0 1 13 6.5C13 10 7 17 7 17Z" fill="none" stroke="#999"/><circle cx="7" cy="6.5" r="2" fill="#999"/></svg><div class="loc">Noida - Sector 18</div></div>
  <div class="card"><div class="photo" role="img" aria-label="Shopping complex block render" style="background:linear-gradient(180deg,#6fa2d8,#b7a48c)"></div><h3>City Core - SCO In Sector</h3><div class="kind">Shopping Complex</div><svg width="14" height="18" viewBox="0 0 14 18"><path d="M7 17C7 17 1 10 1 6.5A6 6 0 0 1 13 6.5C13 10 7 17 7 17Z" fill="none" stroke="#999"/><circle cx="7" cy="6.5" r="2" fill="#999"/></svg><div class="loc">Mohali - Sihon Majra</div></div>
  <div class="card"><div class="photo" role="img" aria-label="Retail building under blue sky" style="background:linear-gradient(180deg,#3f78c0,#b89c7c)"></div><h3>The Opal Sector 49</h3><div class="kind">Retail Malls</div><svg width="14" height="18" viewBox="0 0 14 18"><path d="M7 17C7 17 1 10 1 6.5A6 6 0 0 1 13 6.5C13 10 7 17 7 17Z" fill="none" stroke="#999"/><circle cx="7" cy="6.5" r="2" fill="#999"/></svg><div class="loc">Gurgaon - Sector 102</div></div>
  <div class="card"><div class="photo" role="img" aria-label="Mall and tower at dusk" style="background:linear-gradient(180deg,#2a4a78,#6b7c92)"></div><h3>Skyline Walk Mall</h3><div class="kind">Shopping Complex</div><svg width="14" height="18" viewBox="0 0 14 18"><path d="M7 17C7 17 1 10 1 6.5A6 6 0 0 1 13 6.5C13 10 7 17 7 17Z" fill="none" stroke="#999"/><circle cx="7" cy="6.5" r="2" fill="#999"/></svg><div class="loc">Chennai - Aminjikarai</div></div>
  <div class="card"><div class="photo" role="img" aria-label="Illuminated mall at night" style="background:linear-gradient(180deg,#14213a,#8a5a3a)"></div><h3>Vega Mall</h3><div class="kind">Retail Malls</div><svg width="14" height="18" viewBox="0 0 14 18"><path d="M7 17C7 17 1 10 1 6.5A6 6 0 0 1 13 6.5C13 10 7 17 7 17Z" fill="none" stroke="#999"/><circle cx="7" cy="6.5" r="2" fill="#999"/></svg><div class="loc">Bangalore - Malleshwaram</div></div>
  <div class="card"><div class="photo" role="img" aria-label="Curved mall building at night" style="background:linear-gradient(180deg,#10203e,#3c5a8a)"></div><h3>Triad Square</h3><div class="kind">Retail Malls</div><svg width="14" height="18" viewBox="0 0 14 18"><path d="M7 17C7 17 1 10 1 6.5A6 6 0 0 1 13 6.5C13 10 7 17 7 17Z" fill="none" stroke="#999"/><circle cx="7" cy="6.5" r="2" fill="#999"/></svg><div class="loc">Dwarka Expressway - Gurgaon</div></div>
  <div class="card"><div class="photo" role="img" aria-label="Mall atrium with escalators" style="background:linear-gradient(180deg,#8a9aa0,#5a6a5e)"></div><h3>Greenway Mall</h3><div class="kind">Retail Malls</div><svg width="14" height="18" viewBox="0 0 14 18"><path d="M7 17C7 17 1 10 1 6.5A6 6 0 0 1 13 6.5C13 10 7 17 7 17Z" fill="none" stroke="#999"/><circle cx="7" cy="6.5" r="2" fill="#999"/></svg><div class="loc">Hunsur Main Road - Mysore</div></div>
</div>

<section class="abs extras">
  <div class="col" style="left:60px;width:300px">
    <h4>Listing Alert</h4>
    <p>Subscribe for fortnightly email update on new<br>listings @ Lotstallmart</p>
  </div>
  <div class="input" style="left:90px;top:222px;width:251px">Enter Email</div>
  <div class="input sel" style="left:90px;top:268px;width:251px">Select Location</div>
  <div class="hint" style="left:90px;top:306px">(select retail format of interest)</div>
  <div class="input sel" style="left:90px;top:326px;width:251px">Select City</div>
  <div class="hint" style="left:90px;top:364px">(select cities of interest)</div>
  <div class="btn" style="left:90px;top:425px;width:150px">Subscribe</div>

  <div class="col" style="left:437px;width:300px">
    <h4>Editor's Choice</h4>
    <p style="top:328px;left:20px;width:260px;text-align:left;font-size:10px">A "Select" listing of retail properties handpicked by our editors based on their own positive evaluation on parameters &amp; attributes such as design concept, location, developer, success potential. So read on to check out for yourself...</p>
  </div>
  <div class="editor-img" role="img" aria-label="Modern office tower against the sky"></div>
  <div class="btn" style="left:538px;top:425px;width:102px">More</div>

  <div class="col" style="left:830px;width:300px">
    <h4>Mart Wizards</h4>
    <p>Post your retail space requirement with us<br>and our experts shall get back with suitable<br>options and even help you in your transaction.<br>This is a Free Service!</p>
  </div>
  <div class="input" style="left:853px;top:224px;width:254px">Enter Email</div>
  <div class="input" style="left:853px;top:264px;width:254px">Mobile</div>
  <div class="input" style="left:853px;top:304px;width:254px;height:70px">Message</div>
  <div class="btn" style="left:850px;top:425px;width:98px">Send</div>
</section>

<footer class="abs footer">
  <div class="brand"><span class="brand-dot"></span><span class="brand-name">lotstallmart</span></div>
  <h5 style="left:468px">About Retail Hub</h5>
  <ul class="links" style="left:468px"><li>About Us</li><li>Privacy Policy</li><li>Terms of Use</li><li>Contact Us</li><li>Site Map</li></ul>
  <ul class="links" style="left:592px"><li>Retail Malls</li><li>Shopping Complex</li><li>High Street Shops</li><li>Retail Warehouses</li></ul>
  <h5 style="left:775px">About Lotstallmart</h5>
  <p class="about">Lotstallmart.com is a specialised web based platform for retail space, featuring properties across India under various formats such as Retail Malls, Shopping Complexes, High-street Shops. Also featured are Retail Warehouses which provide the logistic back-end for the retail business. Lotstallmart.com is useful to various category of users as follows: a. Devel.</p>
  <div class="rule-w"></div>
  <div class="social"><span></span><span></span><span></span><span></span></div>
  <div class="rule-c"></div>
  <div class="addr" style="top:322px">Unit 406, 4th Floor, Lorem Ipsum is simply, Sector x, Gurgaon - 122002<br>Phone : 000-000-0000 &nbsp;&nbsp; Fax : 000 - 000 - 0000</div>
  <div class="addr" style="top:392px;font-size:10px">Copyright © 2015 RetailHubIndia.com. All rights reserved.</div>
</footer>

</body>
</html>
```